Independent book publisher needs book cover design

We need a full book cover (front, back and spine) designed for one of our authors and a detailed specification doc is attached.

The book is titled, "Steady Hands, Quiet Harbors: A Field Guide to Backup Routes; since drafting a route is gentler than cleaning up the wreckage". It outlines a structured process by which women can avoid or reduce risk and uncertainty in their lives. It is written for women who have a lot to lose.

A good metaphor for this book would be one that is related to prevention or rescue. The author prefers something based on a lifeboat or perhaps an empty life preserver (maybe with sinking ship and sharks in background). Other ideas are welcomed.

Target Market(s)

It is written for women who have a lot to lose.

Industry/Entity Type

Book Publisher

Requirements
Must have
• See attachment.
• Please note:
• The uploaded file has been updated and a bar code file has been uploaded.

```html
<!DOCTYPE html>
<html lang="en">
<head>
<meta charset="utf-8">
<title>Steady Hands, Quiet Harbors – Book Cover</title>
<link href="https://fonts.googleapis.com/css2?family=Oswald:wght@500;700&family=Roboto+Condensed:wght@400;700&display=swap" rel="stylesheet">
<style>
  :root{
    --stage-top:#6a6a6a;
    --stage-bottom:#3a3a3a;
    --paper:#f6f7f5;
    --red:#c01f2f;
    --red-bright:#e0202c;
    --red-deep:#8e0f1c;
    --ink:#111111;
    --body:#1c1c1c;
    --white:#ffffff;
    --block:#000000;
  }
  *{box-sizing:border-box;margin:0;padding:0}
  html,body{width:1200px;height:999px;overflow:hidden}
  body{
    background:radial-gradient(ellipse at 50% 45%,var(--stage-top),var(--stage-bottom));
    font-family:"Roboto Condensed",Arial,sans-serif;
    position:relative;
  }
  .cover{position:absolute;left:13px;top:90px;width:1174px;height:819px;background:var(--paper);box-shadow:0 2px 10px rgba(0,0,0,.35)}

  /* back cover */
  .back{position:absolute;left:0;top:0;width:570px;height:819px}
  .back-headline{position:absolute;left:43px;top:45px;font-weight:700;font-size:19.5px;line-height:24px;color:var(--red);white-space:nowrap}
  .back-copy{position:absolute;left:44px;top:82px;width:496px;font-size:12.8px;line-height:16.3px;color:var(--body);text-align:justify}
  .back-copy p{margin-bottom:16.3px}
  .back-copy .lead{font-weight:700;font-size:13.6px;line-height:17px;color:var(--ink);margin-bottom:6px;text-align:left}
  .topics{list-style:none}
  .topics li::before{content:"• "}
  .author-bio{position:absolute;left:44px;top:530px;width:340px;font-size:12.8px;line-height:16.3px;color:var(--body);text-align:justify}
  .author-photo{position:absolute;left:397px;top:530px;width:135px;height:160px;background:var(--block);border-radius:12px}
  .barcode-slot{position:absolute;left:314px;top:705px;width:214px;height:72px;background:var(--block);color:var(--white);font-weight:700;font-size:13px;display:flex;align-items:center;justify-content:center}
  .website{position:absolute;left:48px;top:759px;font-weight:700;font-size:12.5px;color:var(--ink)}

  /* spine */
  .spine{position:absolute;left:570px;top:0;width:35px;height:819px;background:var(--red)}
  .spine-text{position:absolute;left:35px;top:82px;width:670px;transform-origin:0 0;transform:rotate(90deg);display:flex;justify-content:space-between;align-items:center;height:35px;color:var(--white);font-weight:700;font-size:21px;white-space:nowrap}

  /* front cover */
  .front{position:absolute;left:605px;top:0;width:569px;height:819px;overflow:hidden}
  .front-art{position:absolute;left:0;top:0}
  .title{position:absolute;left:22px;top:14px;font-family:"Oswald",Impact,sans-serif;text-transform:uppercase;line-height:1}
  .title .big{font-weight:700;font-size:62px;color:var(--red);letter-spacing:.5px}
  .title .small{font-weight:700;font-size:29px;color:var(--ink);letter-spacing:.5px}
  .title .row{display:block;height:66px}
  .title .row.tail{margin-top:2px;margin-left:4px}
  .author-front{position:absolute;left:0;width:569px;top:776px;text-align:center;font-family:"Oswald",Impact,sans-serif;font-weight:500;font-size:28px;letter-spacing:5px;color:var(--red)}
</style>
</head>
<body>
<div class="cover">

  <section class="back">
    <h2 class="back-headline">Drafting a Route Is Gentler Than Cleaning Up the Wreckage</h2>
    <div class="back-copy">
      <p>Throughout history, women have always found themselves in an extraordinarily vulnerable position. Not least because, at the heart of family life, they often have the responsibility for bringing up and nurturing children.</p>
      <p>This book outlines a structured process by which women can avoid or reduce risk and uncertainty in their lives. It is written for women who have a lot to lose. Women, like you.</p>
      <p>In her professional life, the Author met countless women who, through no fault of their own, faced financial, physical and psychological distress because of redundancy, divorce, and critical illness. Some even lost their homes and were admitted to residential care. In every case, there were simple strategies that could have avoided or reduced the impact of these situations.</p>
      <p>You will discover how to make effective contingency plans in case your life does not work out exactly as you originally intended. You will discover how to reduce the risk of financial ruin, and the uncertain future it would create. The author takes you through the fundamentals steps for creating a contingency plan. You will be guided, step by step, through a process to set up a framework to safeguard your hard-earned assets and protect your loved ones from the risk of a future without basic necessities – food, water, clothing and a roof over your head.</p>
      <p class="lead">This book is brimming with tips and insightful case studies and covers every area of your life.</p>
      <ul class="topics">
        <li>Finance</li>
        <li>Relationships</li>
        <li>Health and Wellbeing</li>
        <li>Asset Ownership</li>
        <li>Family and Inheritance</li>
      </ul>
    </div>
    <p class="author-bio">Maren Ashby is a medical doctor and Member of the Guild of Family Physicians (UK). She has over twenty years' experience and has worked in the public health service and overseas missions. Maren has two children and has personally experienced the trauma of divorce; the impact of which was dire and could have been reduced if she had put some basic risk mitigation strategies in place beforehand. In getting through her own divorce, Maren learned some essential lessons for the future. Now she wants to share what she learned, so you don't end up in the same dire situation.</p>
    <div class="author-photo" role="img" aria-label="Author portrait placeholder"></div>
    <div class="barcode-slot">[Barcode]</div>
    <p class="website">www.steadyhandsguide.co.uk</p>
  </section>

  <aside class="spine">
    <div class="spine-text"><span>Steady Hands, Quiet Harbors</span><span>Maren Ashby</span></div>
  </aside>

  <section class="front">
    <svg class="front-art" width="569" height="819" viewBox="0 0 569 819">
      <defs>
        <linearGradient id="sky" x1="0" y1="0" x2="0" y2="1">
          <stop offset="0" stop-color="#a9b2b8"/>
          <stop offset="0.45" stop-color="#d3d6d6"/>
          <stop offset="0.62" stop-color="#b8bcbc"/>
          <stop offset="0.7" stop-color="#cfcac2"/>
          <stop offset="1" stop-color="#8d8579"/>
        </linearGradient>
        <linearGradient id="swoosh" x1="0" y1="0" x2="1" y2="0">
          <stop offset="0" stop-color="#8e0f1c"/>
          <stop offset="0.5" stop-color="#e0202c"/>
          <stop offset="1" stop-color="#c01f2f"/>
        </linearGradient>
      </defs>
      <path role="img" aria-label="Photo: child in a suit holding a briefcase, facing a cloudy sky with hot-air balloons over a wooden deck" d="M0 250 Q330 235 569 112 L569 655 Q300 650 0 610 Z" fill="url(#sky)"/>
      <path d="M0 192 Q320 215 569 58 L569 112 Q330 235 0 250 Z" fill="url(#swoosh)"/>
      <path d="M0 192 Q320 215 569 58 L569 68 Q320 222 0 205 Z" fill="#8e0f1c" opacity=".5"/>
      <path d="M0 610 Q300 650 569 655 L569 700 Q300 700 0 660 Z" fill="url(#swoosh)"/>
      <path d="M0 660 Q300 700 569 700 L569 712 Q290 712 0 672 Z" fill="#8e0f1c" opacity=".55"/>
    </svg>
    <h1 class="title">
      <span class="row"><span class="big">Steady</span> <span class="small">Hands,</span></span>
      <span class="row"><span class="big">Quiet</span></span>
      <span class="row tail"><span class="small">Harbors</span></span>
    </h1>
    <p class="author-front">MAREN ASHBY</p>
  </section>

</div>
</body>
</html>
```